Non Profit Company Looking For New Website

The website for Fernvale Quillstone Heritage Society should offer the viewer beautiful photos that inspire condifence and joy and tap into our love of horses.

We would like to see a website that displays trust, quality and confidence. Needs to be responsive and mobile friendly for all browsers and coded for both Android & IOS.

READ ATTACHED WEBSITE TEMPLATE FOR COMPLETE DETAILS ON WHAT WE ARE LOOKING FOR.

Looking for recommmendations if we should use WordPress/WooCommerce for site or Wordpress with Shopify Plug in or just Shopify.

Must be both desktop and mobile friendly with fast page load speed. Need the ability to edit ourselves.

Industry/Entity Type

Non Profit

Coding

Coded - Design and coding required

Number of Pages Required

5+ page

Requirements
Must have
• We would like to see a website that displays trust, quality and confidence. Needs to be responsive and mobile friendly for all browsers and coded for both Android & IOS.

Looking for recommendations if we should use WordPress/WooCommerce for site or Wordpress with Shopify Plug in or just Shopify.

Logo Colour:
Pantone 7621 C

READ TEMPLATE THAT IS ATTACHED
Nice to have
• Like look of this website as a sample:
https://www.quellbrimtorva.com/

Another similar non profit organization
https://pellaworthcindle.com/

```html
<!DOCTYPE html>
<html lang="en">
<head>
<meta charset="utf-8">
<title>Fernvale Quillstone Heritage Society – Home Page Concepts</title>
<link rel="stylesheet" href="https://fonts.googleapis.com/css2?family=Cinzel:wght@400;600;700&family=Montserrat:ital,wght@0,400;0,500;0,600;1,500&display=swap">
<style>
:root{
  --red:#b8202b;
  --red-soft:#c9343f;
  --ink:#1d1d1d;
  --muted:#6b6b6b;
  --board:#efefef;
  --white:#ffffff;
  --black:#000000;
  --line:#d8d8d8;
}
*{box-sizing:border-box;margin:0;padding:0}
html,body{width:840px;height:1200px;overflow:hidden}
body{background:var(--board);font-family:'Montserrat',sans-serif;color:var(--ink);position:relative}
.page{position:absolute;top:62px;width:336px;height:1077px;background:var(--white);overflow:hidden;box-shadow:0 3px 14px rgba(0,0,0,.12)}
.page--classic{left:53px}
.page--alt{left:451px}
.abs{position:absolute}
.center{left:0;right:0;text-align:center}

/* header */
.site-header{left:0;top:0;width:336px;height:31px;background:var(--white)}
.topbar{right:31px;top:5px;font-size:4.7px;color:var(--ink);display:flex;gap:4px;align-items:center}
.topbar .ico{width:4px;height:4px;fill:var(--red)}
.nav{right:31px;top:19px;display:flex;gap:9.5px;font-family:'Cinzel',serif;font-size:4.6px;letter-spacing:.1px}
.nav .is-active{color:var(--red)}
.brand-disc{left:30px;top:-9px;width:70px;height:70px;border-radius:50%;background:var(--white);z-index:3;display:flex;align-items:center;justify-content:center;text-align:center}
.brand-name{font-family:'Cinzel',serif;font-weight:600;font-size:6.4px;line-height:8px;color:var(--red);margin-top:6px}

/* hero */
.hero{left:0;top:31px;width:336px;height:163px;background:linear-gradient(100deg,#9fb08a 0%,#6f8a5a 30%,#3c4a3a 58%,#27231f 75%,#8a7a5e 100%)}
.hero-copy{left:31px;top:86px;font-style:italic;font-weight:500;font-size:10.3px;line-height:13px;color:var(--white)}
.btn{display:flex;align-items:center;justify-content:center;border-radius:9px;font-size:4.8px;font-weight:600;letter-spacing:.1px;text-transform:uppercase}
.btn--red{background:var(--red);color:var(--white)}
.btn--white{background:var(--white);color:var(--ink)}
.btn--black{background:var(--black);color:var(--white)}
.hero-btn{left:31px;top:142px;width:58px;height:17px;font-size:5.4px}

/* intro */
.ornament{left:134px;top:208px;width:67px;height:23px;background:linear-gradient(90deg,#f3d6d8,#f8e7e8);border-radius:2px}
.intro-title{top:229px;font-family:'Cinzel',serif;font-weight:700;font-size:13.4px;letter-spacing:.2px}
.intro-note{top:258px;font-size:4.5px;color:var(--muted)}
.intro-sub{top:272px;font-size:7.3px;font-weight:500}
.intro-body{font-size:4.5px;line-height:7px;color:var(--muted)}
.intro-body--a{top:288px}
.intro-body--b{top:309px}
.intro-btn{left:130px;top:338px;width:76px;height:15px}

/* adopt */
.adopt{left:0;top:377px;width:336px;height:138px}
.page--classic .adopt{background:linear-gradient(90deg,#6a4a3a 0%,#a55a35 40%,#3a2620 62%,#2b2320 100%)}
.page--alt .adopt{background:linear-gradient(90deg,#6a4a3a 0%,#a55a35 40%,#7c2a2a 62%,#8a1f26 100%)}
.adopt-title{left:194px;top:25px;font-family:'Cinzel',serif;font-weight:600;font-size:12.5px;color:var(--white)}
.adopt-copy{left:194px;top:45px;font-size:4.5px;line-height:7px;color:var(--white)}
.adopt-btn{left:194px;top:76px;width:50px;height:15px}

/* horses */
.horses-title{top:531px;font-family:'Cinzel',serif;font-weight:600;font-size:12.5px}
.tile--1{left:31px;top:560px;width:135px;height:89px;background:linear-gradient(180deg,#8fb3dc 0%,#c9daea 55%,#8a8a5a 75%,#6d8b45 100%)}
.tile--2{left:170px;top:560px;width:135px;height:89px;background:linear-gradient(180deg,#d6e4ef 0%,#e4ebef 58%,#5f9a3a 74%,#4f8a2f 100%)}
.tile--3{left:31px;top:652px;width:90px;height:83px;background:linear-gradient(180deg,#c9ccce 0%,#bfc2c2 58%,#8b8066 78%,#6f6552 100%)}
.tile--4{left:123px;top:652px;width:90px;height:83px;background:linear-gradient(180deg,#6f8a4a 0%,#8aa455 45%,#5d7a38 100%)}
.tile--5{left:215px;top:652px;width:90px;height:83px;background:linear-gradient(180deg,#7fb2e0 0%,#b9d6ec 45%,#d9e8ee 60%,#c79a6a 80%,#b07a4a 100%)}
.give-btn{left:132px;top:750px;width:72px;height:15px}

/* contact */
.contact{left:0;top:788px;width:336px;height:201px}
.page--classic .contact{background:linear-gradient(160deg,#c9404a 0%,#c1303b 45%,#b8283a 100%)}
.page--alt .contact{background:linear-gradient(160deg,#f4f4f4 0%,#ececec 50%,#e6e4e4 100%)}
.contact-title{top:14px;font-family:'Cinzel',serif;font-weight:600;font-size:12.5px;line-height:13px}
.contact-sub{top:47px;font-size:4.7px;font-weight:500}
.page--classic .contact-title,.page--classic .contact-sub,.page--classic .info-text{color:var(--white)}
.info-icon{left:31px;width:16px;height:16px;border-radius:50%;display:flex;align-items:center;justify-content:center}
.page--classic .info-icon{border:1px solid var(--white)}
.page--alt .info-icon{border:1px solid var(--red)}
.info-icon svg{width:7px;height:7px}
.page--classic .info-icon svg{fill:var(--white)}
.page--alt .info-icon svg{fill:var(--red)}
.info-icon--pin{top:72px}
.info-icon--call{top:103px}
.info-icon--mail{top:126px}
.info-text{left:53px;font-size:4.4px;line-height:6.3px}
.info-text strong{font-weight:600;font-size:4.8px}
.info-text--pin{top:73px}
.info-text--call{top:103px}
.info-text--mail{top:127px}
.field{background:var(--white);border:1px solid var(--line);font-size:4.3px;color:#8a8a8a;padding:4px 4px}
.field--first{left:135px;top:70px;width:83px;height:14px}
.field--last{left:222px;top:70px;width:83px;height:14px}
.field--phone{left:135px;top:88px;width:83px;height:14px}
.field--email{left:222px;top:88px;width:83px;height:14px}
.field--message{left:135px;top:106px;width:170px;height:28px}
.captcha{left:135px;top:138px;width:73px;height:27px;background:#f9f9f9;border:1px solid var(--line);display:flex;align-items:center;padding:0 5px;gap:4px;font-size:3.8px;color:#444}
.captcha-box{width:6px;height:6px;border:1px solid #bdbdbd;background:var(--white)}
.captcha-mark{margin-left:auto;width:9px;height:9px;background:#9aa7c0;border-radius:1px}
.submit-btn{left:135px;top:169px;width:40px;height:15px}

/* footer */
.site-footer{left:0;top:989px;width:336px;height:88px;background:var(--black);color:var(--white)}
.footer-brand{top:13px;font-family:'Cinzel',serif;font-weight:600;font-size:6px;line-height:7.5px}
.footer-nav{top:41px;display:flex;justify-content:center;gap:9px;font-size:4.5px}
.copyright{top:50px;font-size:4.3px}
.socials{top:59px;display:flex;justify-content:center;gap:2.5px}
.social{width:13.5px;height:13.5px;border-radius:50%;border:1px solid var(--white)}
</style>
</head>
<body>

<!-- Concept A -->
<main class="page page--classic">
  <header class="site-header abs">
    <div class="topbar abs">
      <svg class="ico" viewBox="0 0 10 10"><path d="M2 0.5 4 3 3 4.2c.6 1.3 1.5 2.2 2.8 2.8L7 6l2.5 2L8.4 9.5C4 9.2.8 6 .5 1.6z"/></svg>
      <span>1 555 014 2290</span><span>|</span>
      <svg class="ico" viewBox="0 0 10 10"><path d="M0 2h10v6H0z"/></svg>
      <span>info@fernvalequillstone.org</span>
    </div>
    <nav class="nav abs"><span class="is-active">Home</span><span>About</span><span>Adopt</span><span>Horses</span><span>Donate/Shop</span><span>Contact</span></nav>
  </header>
  <div class="brand-disc abs"><div class="brand-name">Fernvale<br>Quillstone</div></div>

  <section class="hero abs" role="img" aria-label="Photo of a young rider in a helmet sitting on a dark horse beside a wooden fence, sunlit trees behind"></section>
  <p class="hero-copy abs">We support and develop<br>retired thoroughbred<br>racehorses for their next<br>chapter in life</p>
  <a class="btn btn--red hero-btn abs">Donate Now!</a>

  <div class="ornament abs" role="img" aria-label="Red line drawing of a running horse"></div>
  <h1 class="intro-title abs center">Retire. Retrain. Rehome.</h1>
  <p class="intro-note abs center">Fernvale Quillstone Heritage Society (FQHS) is a registered not-for-profit organization in Westmere.</p>
  <h2 class="intro-sub abs center">What is Fernvale Quillstone?</h2>
  <p class="intro-body intro-body--a abs center">The health, safety and welfare of our equine athletes does not end at the finish line, and<br>retirement and aftercare are critical to the success of the racing industry.</p>
  <p class="intro-body intro-body--b abs center">Aftercare is the safe placement of racehorses after their careers as racehorse are<br>completed. Some horses might retire to the breeding shed or broodmare bands, while<br>others are retrained for second careers.</p>
  <a class="btn btn--red intro-btn abs">Learn More About Us</a>

  <section class="adopt abs" role="img" aria-label="Photo of a smiling woman in a plaid shirt greeting a chestnut horse in a barn">
    <h2 class="adopt-title abs">Adopt a Horse</h2>
    <p class="adopt-copy abs">Fernvale Quillstone Heritage is committed to<br>helping match you with the perfect horse.</p>
    <a class="btn btn--red adopt-btn abs">Adopt Now</a>
  </section>

  <h2 class="horses-title abs center">Horses</h2>
  <div class="tile tile--1 abs" role="img" aria-label="Chestnut horse standing in a meadow under a blue sky"></div>
  <div class="tile tile--2 abs" role="img" aria-label="Chestnut horse on green grass"></div>
  <div class="tile tile--3 abs" role="img" aria-label="Chestnut horse standing on a hillside"></div>
  <div class="tile tile--4 abs" role="img" aria-label="Dark bay pony in a green paddock"></div>
  <div class="tile tile--5 abs" role="img" aria-label="Chestnut horse on sand in front of a white fence"></div>
  <a class="btn btn--red give-btn abs">More Ways to Give</a>

  <section class="contact abs" role="img" aria-label="Faded red-tinted photo of a horse behind the contact form">
    <h2 class="contact-title abs center">Have a Question or<br>Need More Information?</h2>
    <p class="contact-sub abs center">Give us a call or use the form below</p>
    <div class="info-icon info-icon--pin abs"><svg viewBox="0 0 10 10"><path d="M5 0C3 0 1.6 1.5 1.6 3.4 1.6 6 5 10 5 10s3.4-4 3.4-6.6C8.4 1.5 7 0 5 0zm0 4.6a1.2 1.2 0 110-2.4 1.2 1.2 0 010 2.4z"/></svg></div>
    <p class="info-text info-text--pin abs"><strong>LOCATION</strong><br>48 Quarry Lane<br>Marrowick, LA 100000</p>
    <div class="info-icon info-icon--call abs"><svg viewBox="0 0 10 10"><path d="M2 0.5 4 3 3 4.2c.6 1.3 1.5 2.2 2.8 2.8L7 6l2.5 2L8.4 9.5C4 9.2.8 6 .5 1.6z"/></svg></div>
    <p class="info-text info-text--call abs"><strong>CALL US</strong><br>1 555 014 2290</p>
    <div class="info-icon info-icon--mail abs"><svg viewBox="0 0 10 10"><path d="M0 2h10v6H0z"/></svg></div>
    <p class="info-text info-text--mail abs"><strong>EMAIL US</strong><br>info@fernvalequillstone.org</p>
    <div class="field field--first abs">First Name</div>
    <div class="field field--last abs">Last Name</div>
    <div class="field field--phone abs">Your Phone</div>
    <div class="field field--email abs">Your Email</div>
    <div class="field field--message abs">How can we help you?</div>
    <div class="captcha abs"><span class="captcha-box"></span><span>I'm not a robot</span><span class="captcha-mark"></span></div>
    <a class="btn btn--black submit-btn abs">Submit</a>
  </section>

  <footer class="site-footer abs">
    <div class="footer-brand abs center">Fernvale<br>Quillstone</div>
    <nav class="footer-nav abs center"><span>Home</span><span>About</span><span>Adopt</span><span>Horses</span><span>Donate/Shop</span><span>Contact</span></nav>
    <p class="copyright abs center">© 2021 Fernvale Quillstone Heritage, All rights reserved</p>
    <div class="socials abs center"><span class="social"></span><span class="social"></span><span class="social"></span><span class="social"></span></div>
  </footer>
</main>

<!-- Concept B -->
<main class="page page--alt">
  <header class="site-header abs">
    <div class="topbar abs">
      <svg class="ico" viewBox="0 0 10 10"><path d="M2 0.5 4 3 3 4.2c.6 1.3 1.5 2.2 2.8 2.8L7 6l2.5 2L8.4 9.5C4 9.2.8 6 .5 1.6z"/></svg>
      <span>1 555 014 2290</span><span>|</span>
      <svg class="ico" viewBox="0 0 10 10"><path d="M0 2h10v6H0z"/></svg>
      <span>info@fernvalequillstone.org</span>
    </div>
    <nav class="nav abs"><span class="is-active">Home</span><span>About</span><span>Adopt</span><span>Horses</span><span>Donate/Shop</span><span>Contact</span></nav>
  </header>
  <div class="brand-disc abs"><div class="brand-name">Fernvale<br>Quillstone</div></div>

  <section class="hero abs" role="img" aria-label="Photo of a young rider in a helmet sitting on a dark horse beside a wooden fence, sunlit trees behind"></section>
  <p class="hero-copy abs">We support and develop<br>retired thoroughbred<br>racehorses for their next<br>chapter in life</p>
  <a class="btn btn--red hero-btn abs">Donate Now!</a>

  <div class="ornament abs" role="img" aria-label="Red line drawing of a running horse"></div>
  <h1 class="intro-title abs center">Retire. Retrain. Rehome.</h1>
  <p class="intro-note abs center">Fernvale Quillstone Heritage Society (FQHS) is a registered not-for-profit organization in Westmere.</p>
  <h2 class="intro-sub abs center">What is Fernvale Quillstone?</h2>
  <p class="intro-body intro-body--a abs center">The health, safety and welfare of our equine athletes does not end at the finish line, and<br>retirement and aftercare are critical to the success of the racing industry.</p>
  <p class="intro-body intro-body--b abs center">Aftercare is the safe placement of racehorses after their careers as racehorse are<br>completed. Some horses might retire to the breeding shed or broodmare bands, while<br>others are retrained for second careers.</p>
  <a class="btn btn--red intro-btn abs">Learn More About Us</a>

  <section class="adopt abs" role="img" aria-label="Photo of a smiling woman in a plaid shirt greeting a chestnut horse, fading into a red panel">
    <h2 class="adopt-title abs">Adopt a Horse</h2>
    <p class="adopt-copy abs">Fernvale Quillstone Heritage is committed to<br>helping match you with the perfect horse.</p>
    <a class="btn btn--white adopt-btn abs">Adopt Now</a>
  </section>

  <h2 class="horses-title abs center">Horses</h2>
  <div class="tile tile--1 abs" role="img" aria-label="Chestnut horse standing in a meadow under a blue sky"></div>
  <div class="tile tile--2 abs" role="img" aria-label="Chestnut horse on green grass"></div>
  <div class="tile tile--3 abs" role="img" aria-label="Chestnut horse standing on a hillside"></div>
  <div class="tile tile--4 abs" role="img" aria-label="Dark bay pony in a green paddock"></div>
  <div class="tile tile--5 abs" role="img" aria-label="Chestnut horse on sand in front of a white fence"></div>
  <a class="btn btn--red give-btn abs">More Ways to Give</a>

  <section class="contact abs" role="img" aria-label="Faint pale photo of a horse behind the contact form">
    <h2 class="contact-title abs center">Have a Question or<br>Need More Information?</h2>
    <p class="contact-sub abs center">Give us a call or use the form below</p>
    <div class="info-icon info-icon--pin abs"><svg viewBox="0 0 10 10"><path d="M5 0C3 0 1.6 1.5 1.6 3.4 1.6 6 5 10 5 10s3.4-4 3.4-6.6C8.4 1.5 7 0 5 0zm0 4.6a1.2 1.2 0 110-2.4 1.2 1.2 0 010 2.4z"/></svg></div>
    <p class="info-text info-text--pin abs"><strong>LOCATION</strong><br>48 Quarry Lane<br>Marrowick, LA 100000</p>
    <div class="info-icon info-icon--call abs"><svg viewBox="0 0 10 10"><path d="M2 0.5 4 3 3 4.2c.6 1.3 1.5 2.2 2.8 2.8L7 6l2.5 2L8.4 9.5C4 9.2.8 6 .5 1.6z"/></svg></div>
    <p class="info-text info-text--call abs"><strong>CALL US</strong><br>1 555 014 2290</p>
    <div class="info-icon info-icon--mail abs"><svg viewBox="0 0 10 10"><path d="M0 2h10v6H0z"/></svg></div>
    <p class="info-text info-text--mail abs"><strong>EMAIL US</strong><br>info@fernvalequillstone.org</p>
    <div class="field field--first abs">First Name</div>
    <div class="field field--last abs">Last Name</div>
    <div class="field field--phone abs">Your Phone</div>
    <div class="field field--email abs">Your Email</div>
    <div class="field field--message abs">How can we help you?</div>
    <div class="captcha abs"><span class="captcha-box"></span><span>I'm not a robot</span><span class="captcha-mark"></span></div>
    <a class="btn btn--red submit-btn abs">Submit</a>
  </section>

  <footer class="site-footer abs">
    <div class="footer-brand abs center">Fernvale<br>Quillstone</div>
    <nav class="footer-nav abs center"><span>Home</span><span>About</span><span>Adopt</span><span>Horses</span><span>Donate/Shop</span><span>Contact</span></nav>
    <p class="copyright abs center">© 2021 Fernvale Quillstone Heritage, All rights reserved</p>
    <div class="socials abs center"><span class="social"></span><span class="social"></span><span class="social"></span><span class="social"></span></div>
  </footer>
</main>

</body>
</html>
```